Blow Dry Bar Business Cards

These cards must be eye catching and modern.
You must be willing to work fast and make changes.

Winner will be offered other projects

Files 1 THIS IS THE STYLE CARDS I AM INTRESTED IN!!!
Please be creative, I am paying for my own eye catching design. I need files to be nexa press ready.

COLORS THAT ARE PAINTED INSIDE MY SHOP:
- - - http://www.quorvelpaint.example/en/explore-colors/painter/color-selector.html?colors=4007-3C

- - - http://www.brandivex.example/color/paint-colors/hidden-corridor-d58-2

I want the business cards sleek and modern if you use the logo please correct imperfections. I added the part that says Blow Dry Bar (see website).
Do not be afraid to separate the blow dryer from the name to make the cards look like the file with the pink elephant.

SHOULD INCLUDE
*Blow Dryer (we are a blow dry bar not a salon we do not cut or color so do not include sheers of any kind)
*BUSINESS NAME: Simply Swept Upward - Blow Dry Bar (PLEASE SEE MY WEBSITE)
* Website: SIMPLYSWEPTUPWARD.EXAMPLE
*Phone number (555) 014-2763
Updates

Nexa press said it can be submitted in JPG

http://www.brandivex.example/color/paint-colors/hidden-corridor-d58-2 http://www.quorvelpaint.example/en/explore-colors/painter/color-selector.html?colors=4007-3C ^^^^ These links will take you to the color paint that is painted inside my shop.

Target Market(s)

AGES 18 - 55 WOMEN
HIGH END MARKET

Industry/Entity Type

Salon

Requirements
Must have
• SEE COLOR EXAMPLE FILE
BLOW DRYER
UNIQUE
I LIKE THE CARD WITH THE PINK ELEPHANT THE BEST
Nice to have
• BE AS CREATIVE AND MODERN AS POSSIBLE DO NOT COPY ANY OF THE CARDS BELOW.
Should not have
• SCISSORS
PINK

```html
<!DOCTYPE html>
<html lang="en">
<head>
<meta charset="utf-8">
<title>Simply Swept Upward – Business Cards</title>
<link rel="stylesheet" href="https://fonts.googleapis.com/css2?family=Roboto+Slab:wght@400&family=Open+Sans:wght@400;600&display=swap">
<style>
  :root {
    --backdrop: #2b2b2e;
    --card: #070707;
    --card-edge: #1c1c1c;
    --teal: #5ec3cb;
    --cocoa: #4b2f30;
    --white: #f4f4f4;
    --wave-band: #161616;
  }
  * { margin: 0; padding: 0; box-sizing: border-box; }
  html, body {
    width: 1200px; height: 800px; overflow: hidden;
    background: var(--backdrop);
  }
  .stage { position: relative; width: 1200px; height: 800px; }
  .card {
    position: absolute; top: 257px;
    width: 500px; height: 286px;
    background: var(--card);
    border: 1px solid var(--card-edge);
    border-radius: 16px;
    overflow: hidden;
  }
  .card--back { left: 70px; }
  .card--front { left: 630px; }

  .brand-name {
    font-family: "Roboto Slab", Georgia, serif;
    font-weight: 400;
    white-space: nowrap;
    line-height: 1;
  }
  .brand-mark {
    position: absolute;
    width: 58px; height: 58px;
  }

  /* back */
  .card--back .brand-mark {
    left: 318px; top: 78px;
    background: var(--cocoa);
  }
  .card--back .brand-name {
    position: absolute; left: 110px; top: 146px;
    font-size: 36px; color: var(--cocoa);
  }

  /* front */
  .card--front .brand-mark {
    right: 38px; top: 26px;
    background: var(--teal);
  }
  .front-identity {
    position: absolute; right: 38px; top: 92px; text-align: right;
  }
  .front-identity .brand-name {
    font-size: 36px; color: var(--teal);
  }
  .business-name {
    font-family: "Open Sans", Arial, sans-serif;
    font-size: 21px; color: var(--white); line-height: 1.2; margin-top: 4px;
  }
  .business-type {
    font-family: "Open Sans", Arial, sans-serif;
    font-size: 13px; color: var(--white);
  }
  .wave-band {
    position: absolute; left: 0; right: 0; top: 178px; height: 22px;
    background: linear-gradient(90deg, var(--wave-band), #1e1e1e, var(--wave-band));
  }
  .contact {
    position: absolute; left: 22px; bottom: 20px;
    list-style: none;
    font-family: "Open Sans", Arial, sans-serif;
    color: var(--white); letter-spacing: 0.3px;
  }
  .contact li { display: flex; align-items: center; gap: 9px; line-height: 1.45; }
  .contact .phone { font-size: 15px; }
  .contact .web { font-size: 17px; }
  .contact svg { width: 13px; height: 13px; flex: none; }
</style>
</head>
<body>
<main class="stage">
  <section class="card card--back" aria-label="Card back">
    <div class="brand-mark" role="img" aria-label="Blow dryer mark"></div>
    <p class="brand-name">Swept Upward</p>
  </section>

  <section class="card card--front" aria-label="Card front">
    <div class="brand-mark" role="img" aria-label="Blow dryer mark"></div>
    <div class="front-identity">
      <p class="brand-name">Swept Upward</p>
      <p class="business-name">Simply Swept Upward</p>
      <p class="business-type">Blow Dry Bar</p>
    </div>
    <div class="wave-band" role="img" aria-label="Faint row of flowing hair waves"></div>
    <ul class="contact">
      <li class="phone">
        <svg viewBox="0 0 16 16" aria-hidden="true"><path fill="var(--teal)" d="M3 1h3l1.5 4-2 1.3a9 9 0 0 0 4.2 4.2L11 8.5l4 1.5v3a2 2 0 0 1-2 2A13 13 0 0 1 1 3a2 2 0 0 1 2-2z"/></svg>
        (555) 014-2763
      </li>
      <li class="web">
        <svg viewBox="0 0 16 16" aria-hidden="true"><g fill="none" stroke="var(--teal)" stroke-width="1.6"><circle cx="8" cy="8" r="6.5"/><ellipse cx="8" cy="8" rx="3" ry="6.5"/><path d="M1.5 8h13"/></g></svg>
        WWW.SIMPLYSWEPTUPWARD.EXAMPLE
      </li>
    </ul>
  </section>
</main>
</body>
</html>
```